Korvath Supply Website Redesign

Currently korvathsupply.example is focussed on fulfillment and transport from various products in the BBQ segment. However, no we want to update our business activities to Product Development, Brand Development, Online Positioning, Logistics & Aftersales, and Promotional BBQs. We will be a business for Outdoor Leisure Development from A to Z.

Therefore, we need a brand new website. The colours of the current website may be the same. However, i'd like to keep it clean. More white and use blue and green as accent colours. It is a business to business organization so the website should be looking formal and corporate. However we sell fun products so not too formal and corporate.

Pages we need; Home, About, Contact, Our Services (+ page per service) a place to share our news/blogs.

I have added some sort of mock up of an idea. However it needs some finetuning.

Target Market(s)

Businesses

Industry/Entity Type

Corporate/Logistics/Marketing

Coding

Coded - Design and coding required

Colors

Designer to choose colors to be used in the design.

Requirements
Must have
• Show clear distinguishing of the different services we provide (Product Development, Brand Development, Online Positioning, Logistics & Aftersales and Promotional BBQs). Every service should have its own page too. Besides, I would like to have a blog page to share relevant content.
Nice to have
• Show that we are the expert in Outdoor LEisure Development from A to Z
Should not have
• Be too informal. It may be semi-formal

```html
<!DOCTYPE html>
<html lang="en">
<head>
<meta charset="utf-8">
<title>Korvath Supply – Home</title>
<link rel="stylesheet" href="https://fonts.googleapis.com/css2?family=Montserrat:wght@500;600;700;800&family=Roboto:wght@400&display=swap">
<style>
:root{
  --stage:#2d2e30;
  --white:#ffffff;
  --teal:#46707d;
  --teal-dark:#2f5866;
  --navy:#1f4c6b;
  --green:#3fae49;
  --green-dark:#2f9139;
  --ink:#3f6b78;
}
*{margin:0;padding:0;box-sizing:border-box}
html,body{width:995px;height:1200px;overflow:hidden;background:var(--stage)}
body{position:relative;font-family:"Montserrat",sans-serif}
.page{position:absolute;top:60px;width:784px;height:1890px;background:var(--white);transform:scale(0.5715);transform-origin:0 0;overflow:hidden}
.page--default{left:30px}
.page--hover{left:503.5px}
.abs{position:absolute}

/* header */
.site-header{left:0;top:0;width:784px;height:60px;background:var(--white);z-index:5}
.brand{left:57px;top:19px;display:flex;align-items:center;gap:7px;font-weight:800;font-size:17px;line-height:22px;color:var(--ink);white-space:nowrap}
.brand-dot{width:18px;height:18px;border-radius:50%;background:var(--green);flex:none}
.nav a{position:absolute;top:24px;font-size:10px;font-weight:600;color:var(--ink);text-decoration:none;letter-spacing:.2px;white-space:nowrap}
.nav a.active{color:var(--green)}
.nav .active-bar{position:absolute;left:258px;top:0;width:42px;height:4px;background:var(--green)}
.nav a.tel{color:var(--green)}

/* hero */
.hero-photo{left:0;top:60px;width:784px;height:440px;background:linear-gradient(115deg,#1f4c6b 0%,#245a78 38%,#3a5f7c 52%,#8a6a55 62%,#5b3f66 72%,#2c5570 85%,#1d5a6f 100%)}
.hero-curve{left:0;top:380px}
.hero-title{left:85px;top:133px;color:var(--white);font-size:31px;font-weight:700;line-height:37.5px;letter-spacing:.3px}

/* services */
.service{width:132px;height:207px;top:378px;border-radius:66px;border:5px solid var(--white);box-shadow:0 0 0 1px #e3e8ea;overflow:hidden;text-align:center;color:var(--white)}
.service--teal{background:var(--teal)}
.service--green{background:var(--green)}
.service-icon{position:absolute;left:24px;top:27px;width:74px;height:74px;border-radius:50%;background:rgba(0,0,0,.14);display:flex;align-items:center;justify-content:center}
.service-name{position:absolute;left:0;right:0;top:119px;font-size:11.5px;font-weight:700;line-height:14px}
.service-more{position:absolute;left:41px;bottom:-30px;width:40px;height:40px;border-radius:50%;font-size:11px;font-weight:700;line-height:18px}
.service--teal .service-more{background:var(--green)}
.service--green .service-more{background:var(--teal)}
.service--open{height:290px;border-radius:70px}
.service--open .service-icon{box-shadow:0 0 0 6px rgba(255,255,255,.08)}
.service-text{position:absolute;left:18px;right:18px;top:157px;font-family:"Roboto",sans-serif;font-size:8.5px;line-height:11px;opacity:.85}
.service-btn{position:absolute;left:28px;top:236px;width:70px;height:20px;border-radius:10px;background:var(--teal);font-size:7.5px;font-weight:700;line-height:20px}

/* intro */
.intro-photo{left:0;top:760px;width:784px;height:297px;background:linear-gradient(180deg,#ffffff 0%,#dfe6ee 20%,#8ba0bb 48%,#6f7f96 70%,#8a7a5a 100%)}
.intro-title{left:0;width:784px;top:672px;text-align:center;font-size:27px;font-weight:700}
.green{color:var(--green)}
.teal{color:var(--ink)}
.intro-text{left:182px;width:465px;top:726px;text-align:center;font-family:"Roboto",sans-serif;font-size:12.6px;line-height:16.3px;color:var(--ink)}

/* news */
.news-title{left:0;width:784px;top:1128px;text-align:center;font-size:28px;font-weight:700}
.news-card{overflow:hidden;color:var(--white);text-align:center}
.news-card--wide-a{left:85px;top:1185px;width:325px;height:168px;border-radius:84px;background:linear-gradient(135deg,#1f3550,#2f5a80 55%,#c09a55)}
.news-card--wide-b{left:85px;top:1364px;width:325px;height:168px;border-radius:84px;background:linear-gradient(135deg,#4a5f75,#b58c5c 50%,#3b4655)}
.news-card--tall{left:412px;top:1185px;width:287px;height:358px;border-radius:143px;background:linear-gradient(160deg,#3b4d66,#6a7a92 45%,#2e3240)}
.news-shade{position:absolute;inset:0;background:linear-gradient(180deg,rgba(0,0,0,0) 40%,rgba(0,0,0,.45))}
.news-date{position:absolute;width:40px;height:40px;border-radius:50%;background:var(--green);font-weight:700;font-size:12px;line-height:12px;padding-top:9px}
.news-date small{display:block;font-size:7px}
.news-head{position:absolute;left:0;right:0;font-size:14.5px;font-weight:700;line-height:18px}
.news-excerpt{position:absolute;left:45px;right:40px;font-family:"Roboto",sans-serif;font-size:9.5px;line-height:12px}

/* footer */
.footer-band{left:0;top:1570px}
.footer-heading{top:1688px;font-size:15px;font-weight:700;color:var(--white)}
.contact-item{left:85px;display:flex;align-items:center;gap:6px;color:var(--white);font-size:10px;line-height:11px}
.contact-icon{width:20px;height:20px;border-radius:50%;background:var(--green);display:flex;align-items:center;justify-content:center;flex:none}
.footer-brand{left:318px;top:1733px;display:flex;align-items:center;gap:10px;color:var(--white);font-size:25px;line-height:32px;font-weight:800;white-space:nowrap}
.footer-brand .brand-dot{width:28px;height:28px}
.footer-links{left:625px;top:1722px;list-style:none;color:var(--white);font-size:10px;line-height:16px}
.copyright{left:0;width:784px;top:1850px;text-align:center;color:var(--white);font-family:"Roboto",sans-serif;font-size:8.5px}
</style>
</head>
<body>

<!-- Default state -->
<div class="page page--default">
  <div class="abs hero-photo" role="img" aria-label="Aerial night photo of a container ship and port terminal"></div>
  <svg class="abs hero-curve" width="784" height="130" viewBox="0 0 784 130"><path d="M0 107 Q170 70 330 90 Q560 130 784 98 L784 130 L0 130Z" fill="#fff"/></svg>
  <h1 class="abs hero-title">OUTDOOR<br>LEISURE<br>DEVELOPMENT<br>FROM A TO Z</h1>

  <header class="abs site-header">
    <div class="abs brand"><span class="brand-dot"></span>Korvath Supply</div>
    <nav class="nav">
      <span class="active-bar"></span>
      <a class="active" style="left:265px">HOME</a>
      <a style="left:322px">ABOUT</a>
      <a style="left:384px">OUR SERVICES</a>
      <a style="left:482px">CONTACT</a>
      <a style="left:553px">NEWS</a>
      <a class="tel" style="left:619px">TEL: +31 (0)20 555 0143</a>
    </nav>
  </header>

  <div class="abs service service--teal" style="left:120px"><div class="service-icon"><svg width="40" height="40" viewBox="0 0 40 40" fill="none" stroke="#fff" stroke-width="2.4"><circle cx="20" cy="20" r="6"/><circle cx="20" cy="20" r="11" stroke-dasharray="5 3"/><path d="M6 16a15 15 0 0 1 26-6M34 24a15 15 0 0 1-26 6"/></svg></div><div class="service-name">Product<br>Development</div><div class="service-more">+</div></div>
  <div class="abs service service--green" style="left:257px"><div class="service-icon"><svg width="40" height="40" viewBox="0 0 40 40" fill="none" stroke="#fff" stroke-width="2.2"><path d="M7 15h26l-3-7H10z"/><path d="M9 15v17h22V15"/><rect x="13" y="20" width="6" height="12"/><rect x="22" y="20" width="6" height="5"/></svg></div><div class="service-name">Brand<br>Development</div><div class="service-more">+</div></div>
  <div class="abs service service--teal" style="left:393px"><div class="service-icon"><svg width="40" height="40" viewBox="0 0 40 40" fill="none" stroke="#fff" stroke-width="2"><circle cx="19" cy="19" r="13"/><ellipse cx="19" cy="19" rx="6" ry="13"/><path d="M6 19h26M8 12h22M8 26h14"/><path d="M24 24l10 4-4 2-2 4z" fill="#fff"/></svg></div><div class="service-name">Online<br>Positioning</div><div class="service-more">+</div></div>
  <div class="abs service service--green" style="left:530px"><div class="service-icon"><svg width="40" height="40" viewBox="0 0 40 40" fill="none" stroke="#fff" stroke-width="2"><rect x="5" y="20" width="16" height="10"/><path d="M21 23h7l4 4v3H21"/><circle cx="10" cy="32" r="2.5"/><circle cx="27" cy="32" r="2.5"/><path d="M29 17c-4-5-5-7-5-9a5 5 0 0 1 10 0c0 2-1 4-5 9z"/><circle cx="29" cy="8" r="1.6"/></svg></div><div class="service-name">Logistics &amp;<br>Aftersales</div><div class="service-more">+</div></div>

  <div class="abs intro-photo" role="img" aria-label="Two colleagues in hard hats checking stock in a warehouse"></div>
  <h2 class="abs intro-title"><span class="green">WE MAKE THE</span> <span class="teal">DIFFERENCE</span></h2>
  <p class="abs intro-text">Lorem ipsum dolor sit amet, consectetur adiing elit, sed do eiusmod tempor incidid unt u tmini&nbsp; veniam, quis nostrud exercitation ulorellamco laboris nisi ut aliquiquip ex eaquip ex ea co cop ex ea commodo consequat. Duis aute irure dolorlore in reprehenderit in voluptateLorem ipsum dolor sit amet, consectetur adiing elit, sed do eiusmod tempor incidid unt u tmini&nbsp; veniam, quis nostrud exercitation ulorellamco laboris nisi ut aliquiquip</p>

  <h2 class="abs news-title"><span class="green">LATEST</span> <span class="teal">NEWS</span></h2>
  <article class="abs news-card news-card--wide-a" role="img" aria-label="Businessman with digital logistics overlay"><div class="news-shade"></div><div class="news-date" style="left:142px;top:45px">15<small>DEC</small></div><div class="news-head" style="top:112px">Lorem ipsum dolo<br>sit ametconsectetur</div></article>
  <article class="abs news-card news-card--wide-b" role="img" aria-label="Cardboard parcels on a conveyor"><div class="news-shade"></div><div class="news-date" style="left:142px;top:48px">15<small>DEC</small></div><div class="news-head" style="top:112px">Lorem ipsum dolo<br>sit ametconsectetur</div></article>
  <article class="abs news-card news-card--tall" role="img" aria-label="Two warehouse staff walking between shelves"><div class="news-shade"></div><div class="news-date" style="left:129px;top:200px">15<small>DEC</small></div><div class="news-head" style="top:266px">Lorem ipsum dolo<br>sit ametconsectetur</div></article>

  <svg class="abs footer-band" width="784" height="320" viewBox="0 0 784 320"><path d="M0 18 Q392 120 784 18 L784 320 L0 320Z" fill="#46707d"/><path d="M75 28 Q392 95 755 22" fill="none" stroke="#fff" stroke-width="12"/><path d="M75 28 Q392 92 755 22" fill="none" stroke="#3fae49" stroke-width="5"/></svg>
  <h3 class="abs footer-heading" style="left:85px">CONTACT</h3>
  <div class="abs contact-item" style="top:1725px"><span class="contact-icon"><svg width="10" height="12" viewBox="0 0 10 12"><path d="M5 12C1 7 0 5.5 0 4a5 5 0 0 1 10 0c0 1.5-1 3-5 8z" fill="#fff"/><circle cx="5" cy="4" r="1.6" fill="#3fae49"/></svg></span><span>Veldstraat 18<br>4811 AB Havenstad</span></div>
  <div class="abs contact-item" style="top:1755px"><span class="contact-icon"><svg width="10" height="10" viewBox="0 0 10 10"><path d="M2 0l2 2.5-1 1.3a6 6 0 0 0 3.2 3.2l1.3-1L10 8l-1.5 2C4 10 0 6 0 1.5z" fill="#fff"/></svg></span><span>Havenstad Office: +31 (0)20 555 0143</span></div>
  <div class="abs contact-item" style="top:1783px"><span class="contact-icon"><svg width="10" height="8" viewBox="0 0 10 8"><rect width="10" height="8" rx="1" fill="#fff"/><path d="M0 1l5 3.5L10 1" fill="none" stroke="#3fae49" stroke-width="1.2"/></svg></span><span>info@korvathsupply.example</span></div>
  <div class="abs footer-brand"><span class="brand-dot"></span>Korvath Supply</div>
  <h3 class="abs footer-heading" style="left:617px">LINKS</h3>
  <ul class="abs footer-links"><li>Home</li><li>About</li><li>Our Services</li><li>Contact</li><li>News</li></ul>
  <p class="abs copyright">2021 Copyright © Korvath Supply . All rights are reserved.</p>
</div>

<!-- Hover state -->
<div class="page page--hover">
  <div class="abs hero-photo" role="img" aria-label="Aerial night photo of a container ship and port terminal"></div>
  <svg class="abs hero-curve" width="784" height="130" viewBox="0 0 784 130"><path d="M0 107 Q170 70 330 90 Q560 130 784 98 L784 130 L0 130Z" fill="#fff"/></svg>
  <h1 class="abs hero-title">OUTDOOR<br>LEISURE<br>DEVELOPMENT<br>FROM A TO Z</h1>

  <header class="abs site-header">
    <div class="abs brand"><span class="brand-dot"></span>Korvath Supply</div>
    <nav class="nav">
      <span class="active-bar"></span>
      <a class="active" style="left:265px">HOME</a>
      <a style="left:322px">ABOUT</a>
      <a style="left:384px">OUR SERVICES</a>
      <a style="left:482px">CONTACT</a>
      <a style="left:553px">NEWS</a>
      <a class="tel" style="left:619px">TEL: +31 (0)20 555 0143</a>
    </nav>
  </header>

  <div class="abs service service--teal" style="left:120px"><div class="service-icon"><svg width="40" height="40" viewBox="0 0 40 40" fill="none" stroke="#fff" stroke-width="2.4"><circle cx="20" cy="20" r="6"/><circle cx="20" cy="20" r="11" stroke-dasharray="5 3"/><path d="M6 16a15 15 0 0 1 26-6M34 24a15 15 0 0 1-26 6"/></svg></div><div class="service-name">Product<br>Development</div><div class="service-more">+</div></div>
  <div class="abs service service--green" style="left:257px"><div class="service-icon"><svg width="40" height="40" viewBox="0 0 40 40" fill="none" stroke="#fff" stroke-width="2.2"><path d="M7 15h26l-3-7H10z"/><path d="M9 15v17h22V15"/><rect x="13" y="20" width="6" height="12"/><rect x="22" y="20" width="6" height="5"/></svg></div><div class="service-name">Brand<br>Development</div><div class="service-more">+</div></div>
  <div class="abs service service--teal" style="left:393px"><div class="service-icon"><svg width="40" height="40" viewBox="0 0 40 40" fill="none" stroke="#fff" stroke-width="2"><circle cx="19" cy="19" r="13"/><ellipse cx="19" cy="19" rx="6" ry="13"/><path d="M6 19h26M8 12h22M8 26h14"/><path d="M24 24l10 4-4 2-2 4z" fill="#fff"/></svg></div><div class="service-name">Online<br>Positioning</div><div class="service-more">+</div></div>
  <div class="abs service service--green service--open" style="left:526px;width:140px"><div class="service-icon" style="left:28px"><svg width="40" height="40" viewBox="0 0 40 40" fill="none" stroke="#fff" stroke-width="2"><rect x="5" y="20" width="16" height="10"/><path d="M21 23h7l4 4v3H21"/><circle cx="10" cy="32" r="2.5"/><circle cx="27" cy="32" r="2.5"/><path d="M29 17c-4-5-5-7-5-9a5 5 0 0 1 10 0c0 2-1 4-5 9z"/><circle cx="29" cy="8" r="1.6"/></svg></div><div class="service-name">Logistics &amp;<br>Aftersales</div><p class="service-text">Seading elised do ei usmod tempor incidi dunt u tmini veniam, quis nostrud exerci ation ulorellamco lab oris nisi ut aliirur</p><div class="service-btn" style="left:30px">READ MORE</div></div>

  <div class="abs intro-photo" role="img" aria-label="Two colleagues in hard hats checking stock in a warehouse"></div>
  <h2 class="abs intro-title"><span class="green">WE MAKE THE</span> <span class="teal">DIFFERENCE</span></h2>
  <p class="abs intro-text">Lorem ipsum dolor sit amet, consectetur adiing elit, sed do eiusmod tempor incidid unt u tmini&nbsp; veniam, quis nostrud exercitation ulorellamco laboris nisi ut aliquiquip ex eaquip ex ea co cop ex ea commodo consequat. Duis aute irure dolorlore in reprehenderit in voluptateLorem ipsum dolor sit amet, consectetur adiing elit, sed do eiusmod tempor incidid unt u tmini&nbsp; veniam, quis nostrud exercitation ulorellamco laboris nisi ut aliquiquip</p>

  <h2 class="abs news-title"><span class="green">LATEST</span> <span class="teal">NEWS</span></h2>
  <article class="abs news-card news-card--wide-a" role="img" aria-label="Businessman with digital logistics overlay"><div class="news-shade"></div><div class="news-date" style="left:142px;top:45px">15<small>DEC</small></div><div class="news-head" style="top:112px">Lorem ipsum dolo<br>sit ametconsectetur</div></article>
  <article class="abs news-card news-card--wide-b" role="img" aria-label="Cardboard parcels on a conveyor"><div class="news-shade"></div><div class="news-date" style="left:142px;top:48px">15<small>DEC</small></div><div class="news-head" style="top:112px">Lorem ipsum dolo<br>sit ametconsectetur</div></article>
  <article class="abs news-card news-card--tall" role="img" aria-label="Two warehouse staff walking between shelves" style="background:linear-gradient(160deg,#2e3c52,#3d4a60 50%,#1f2430)"><div class="news-shade" style="background:rgba(0,0,0,.3)"></div><div class="news-date" style="left:129px;top:72px">15<small>DEC</small></div><div class="news-head" style="top:138px">Lorem ipsum dolo<br>sit ametconsectetur</div><p class="news-excerpt" style="top:195px">Lorem ipsum dolor sit amet, consectetur adipiscing elit, sed do eiusmod tempor incididunt ut labore et dolore magna aliqua. Quis ipsum suspendisse ultrices</p></article>

  <svg class="abs footer-band" width="784" height="320" viewBox="0 0 784 320"><path d="M0 18 Q392 120 784 18 L784 320 L0 320Z" fill="#46707d"/><path d="M75 28 Q392 95 755 22" fill="none" stroke="#fff" stroke-width="12"/><path d="M75 28 Q392 92 755 22" fill="none" stroke="#3fae49" stroke-width="5"/></svg>
  <h3 class="abs footer-heading" style="left:85px">CONTACT</h3>
  <div class="abs contact-item" style="top:1725px"><span class="contact-icon"><svg width="10" height="12" viewBox="0 0 10 12"><path d="M5 12C1 7 0 5.5 0 4a5 5 0 0 1 10 0c0 1.5-1 3-5 8z" fill="#fff"/><circle cx="5" cy="4" r="1.6" fill="#3fae49"/></svg></span><span>Veldstraat 18<br>4811 AB Havenstad</span></div>
  <div class="abs contact-item" style="top:1755px"><span class="contact-icon"><svg width="10" height="10" viewBox="0 0 10 10"><path d="M2 0l2 2.5-1 1.3a6 6 0 0 0 3.2 3.2l1.3-1L10 8l-1.5 2C4 10 0 6 0 1.5z" fill="#fff"/></svg></span><span>Havenstad Office: +31 (0)20 555 0143</span></div>
  <div class="abs contact-item" style="top:1783px"><span class="contact-icon"><svg width="10" height="8" viewBox="0 0 10 8"><rect width="10" height="8" rx="1" fill="#fff"/><path d="M0 1l5 3.5L10 1" fill="none" stroke="#3fae49" stroke-width="1.2"/></svg></span><span>info@korvathsupply.example</span></div>
  <div class="abs footer-brand"><span class="brand-dot"></span>Korvath Supply</div>
  <h3 class="abs footer-heading" style="left:617px">LINKS</h3>
  <ul class="abs footer-links"><li>Home</li><li>About</li><li>Our Services</li><li>Contact</li><li>News</li></ul>
  <p class="abs copyright">2021 Copyright © Korvath Supply . All rights are reserved.</p>
</div>

</body>
</html>
```